Flip Book Reference Guide for Medical Offices

We are looking to take a PowerPoint presentation and turn it into a flip book for our front office staff to use as a quick reference when needed. We are hoping for someone to take a quick once over of the PowerPoint then take it to the next level and make it look beautiful and professional. Alignment, graphics and clarity of design can make or break these sorts of products… we have the message, now need to ensure it's received and that is where you will come into play.

Industry/Entity Type

Medical

```html
<!DOCTYPE html>
<html lang="en">
<head>
<meta charset="utf-8">
<title>Family Medicine Front Desk Flip Book – Front &amp; Back</title>
<link href="https://fonts.googleapis.com/css2?family=Saira+Extra+Condensed:wght@800&family=Kanit:wght@600&family=Open+Sans:wght@700&display=swap" rel="stylesheet">
<style>
  :root {
    --navy: #1c3566;
    --orange: #f7941d;
    --peach: #fdd3a4;
    --yellow: #f4cd1c;
    --edge: #6e5a14;
    --white: #ffffff;
    --backdrop: #e9eaec;
  }
  * { margin: 0; padding: 0; box-sizing: border-box; }
  html, body { width: 1200px; height: 1200px; overflow: hidden; }
  body {
    background: var(--backdrop);
    position: relative;
    font-family: "Open Sans", Arial, sans-serif;
  }
  .card {
    position: absolute;
    left: 238px;
    width: 724px;
    height: 540px;
    background: var(--white);
    overflow: hidden;
  }
  .card--front { top: 40px; }
  .card--back { top: 620px; }

  .stripe { position: absolute; left: 0; width: 100%; }
  .stripe--orange { background: var(--orange); }
  .stripe--peach { background: var(--peach); }
  .stripe--yellow { background: var(--yellow); }

  .title-band {
    position: absolute;
    left: 0; top: 14px;
    width: 100%; height: 248px;
    background: var(--navy);
  }
  .title-band__text {
    position: absolute;
    left: 74px; top: 100px;
    display: flex;
    flex-direction: column;
    gap: 6px;
    color: var(--white);
    white-space: nowrap;
  }
  .title-band__heading {
    font-family: "Saira Extra Condensed", "Arial Narrow", Arial, sans-serif;
    font-weight: 800;
    font-size: 64px;
    line-height: 1;
    letter-spacing: 0.5px;
  }
  .title-band__sub {
    font-family: "Kanit", Arial, sans-serif;
    font-weight: 600;
    font-size: 38px;
    line-height: 1;
  }

  .brand {
    position: absolute;
    display: flex;
    align-items: center;
    gap: 14px;
    font-family: "Open Sans", Arial, sans-serif;
    font-weight: 700;
    color: var(--orange);
    line-height: 1;
    white-space: nowrap;
  }
  .brand__dot {
    border-radius: 50%;
    background: var(--navy);
    flex: none;
  }
  .brand--small { left: 50px; top: 360px; font-size: 56px; }
  .brand--small .brand__dot { width: 22px; height: 22px; }
  .brand--large { left: 56px; top: 196px; font-size: 74px; }
  .brand--large .brand__dot { width: 28px; height: 28px; }

  .top-band {
    position: absolute;
    left: 0; top: 0;
    width: 100%; height: 24px;
    background: var(--navy);
  }
  .intro-note {
    position: absolute;
    left: 20px; right: 20px; top: 300px;
    text-align: center;
    font-family: "Open Sans", Arial, sans-serif;
    font-weight: 700;
    font-size: 16.5px;
    line-height: 31px;
    color: var(--navy);
    white-space: nowrap;
  }

  .corner { position: absolute; width: 100px; height: 100px; }
  .corner--top-left { left: 0; top: 0; }
  .corner--bottom-right { right: 0; bottom: 0; }
</style>
</head>
<body>

  <section class="card card--front" aria-label="Flip book front cover">
    <div class="stripe stripe--orange" style="top:0;height:6px"></div>
    <div class="stripe stripe--peach" style="top:6px;height:8px"></div>
    <div class="title-band">
      <div class="title-band__text">
        <h1 class="title-band__heading">FAMILY MEDICINE</h1>
        <p class="title-band__sub">Front Desk Flip Book</p>
      </div>
    </div>
    <div class="stripe stripe--orange" style="top:262px;height:7px"></div>
    <div class="stripe stripe--peach" style="top:269px;height:6px"></div>

    <div class="brand brand--small"><span class="brand__dot"></span>BrightPath</div>

    <div class="stripe stripe--yellow" style="bottom:0;height:6px"></div>

    <svg class="corner corner--top-left" viewBox="0 0 100 100">
      <polygon points="0,0 92,0 0,92" fill="var(--yellow)"/>
      <line x1="92" y1="0" x2="0" y2="92" stroke="var(--edge)" stroke-width="3"/>
    </svg>
    <svg class="corner corner--bottom-right" viewBox="0 0 100 100">
      <polygon points="100,8 100,100 8,100" fill="var(--yellow)"/>
      <line x1="100" y1="8" x2="8" y2="100" stroke="var(--edge)" stroke-width="3"/>
    </svg>
  </section>

  <section class="card card--back" aria-label="Flip book back cover">
    <div class="top-band"></div>
    <div class="stripe stripe--orange" style="top:24px;height:7px"></div>
    <div class="stripe stripe--peach" style="top:31px;height:6px"></div>

    <div class="brand brand--large"><span class="brand__dot"></span>BrightPath</div>

    <p class="intro-note">This flip book is meant to be a quick reference guide for the front desk.<br>If further clarification or detail is required please refer to the Standard<br>Operating Procedures (SOPs).</p>

    <div class="stripe stripe--yellow" style="bottom:0;height:6px"></div>

    <svg class="corner corner--top-left" viewBox="0 0 100 100">
      <polygon points="0,0 92,0 0,92" fill="var(--yellow)"/>
      <line x1="92" y1="0" x2="0" y2="92" stroke="var(--edge)" stroke-width="3"/>
    </svg>
    <svg class="corner corner--bottom-right" viewBox="0 0 100 100">
      <polygon points="100,8 100,100 8,100" fill="var(--yellow)"/>
      <line x1="100" y1="8" x2="8" y2="100" stroke="var(--edge)" stroke-width="3"/>
    </svg>
  </section>

</body>
</html>
```